Harbourline Electrical Solutions

On one side. LOGO (underneath:) Commercial Industrial Residential

- NAME & CONTACT DETAILS

Marcus T. Hollings
Project Manager

(Cell icon) (441) 555-0187
(Email icon) hlelectricalsolutions@mailvento.com
(Facebook & Instagram icons )@hlelectricalsolutions

Other side: LOGO - underneath ELECTRICAL CONSTRUCTION & MAINTENANCE . LED LIGHTING & AUTOMATION . LIFE SAFETY SYSTEMS (FIRE ALARM / SECURITY) . DATA & COMMUNICATION

```html
<!DOCTYPE html>
<html lang="en">
<head>
<meta charset="utf-8">
<title>Harbourline Electrical Solutions – Business Card</title>
<link href="https://fonts.googleapis.com/css2?family=Lato:wght@400;700&family=Raleway:wght@500;600&display=swap" rel="stylesheet">
<style>
  :root {
    --teal: #0f5468;
    --teal-ink: #0d4f66;
    --charcoal: #4a4a4a;
    --grey-text: #444444;
    --paper: #ffffff;
    --backdrop: #dcdcdc;
  }
  * { margin: 0; padding: 0; box-sizing: border-box; }
  html, body { width: 1200px; height: 802px; overflow: hidden; background: var(--backdrop); }
  .stage { position: relative; width: 1200px; height: 802px; }

  .card {
    position: absolute; top: 274px; width: 443px; height: 264px;
    overflow: hidden;
  }
  .card--front { left: 136px; background: var(--paper); }
  .card--back { left: 624px; background: var(--teal); }

  /* front */
  .holder { position: absolute; left: 20px; top: 29px; }
  .holder__name {
    font-family: 'Lato', sans-serif; font-weight: 700; font-size: 15.5px;
    color: var(--teal-ink); letter-spacing: 0.1px; line-height: 1;
  }
  .holder__role {
    font-family: 'Lato', sans-serif; font-size: 12.5px; color: var(--grey-text);
    margin-top: 3px;
  }

  .wordmark {
    position: absolute; display: flex; align-items: center; gap: 10px;
    font-family: 'Raleway', sans-serif; font-weight: 600;
    text-transform: uppercase; letter-spacing: 2.2px; line-height: 1.15;
  }
  .wordmark__square { width: 14px; height: 14px; flex: none; }
  .wordmark--front { right: 26px; top: 84px; color: var(--teal-ink); font-size: 13.5px; }
  .wordmark--front .wordmark__square { background: var(--teal-ink); }
  .wordmark--back { left: 50%; top: 82px; transform: translateX(-50%); color: #fff; font-size: 16.5px; }
  .wordmark--back .wordmark__square { background: #fff; width: 18px; height: 18px; }

  .sectors {
    position: absolute; right: 26px; top: 136px;
    font-family: 'Lato', sans-serif; font-size: 12px; color: var(--grey-text);
    letter-spacing: 0.1px;
  }

  .contact { position: absolute; left: 20px; top: 211px; font-family: 'Lato', sans-serif; font-size: 13px; color: var(--grey-text); }
  .contact__row { display: flex; align-items: center; gap: 5px; height: 16px; }
  .contact__row svg { flex: none; }

  .social { position: absolute; right: 26px; top: 208px; text-align: right; font-family: 'Lato', sans-serif; font-size: 13px; color: var(--grey-text); }
  .social__dots { display: flex; justify-content: flex-end; gap: 4px; margin-bottom: 3px; }
  .social__dot { width: 19px; height: 19px; border: 1.3px solid var(--teal-ink); border-radius: 50%; }

  .front-bands { position: absolute; left: 0; bottom: 0; }

  /* back */
  .back__rule { position: absolute; left: 0; top: 198px; width: 100%; height: 1.5px; background: #fff; }
  .services {
    position: absolute; left: 0; top: 199.5px; width: 100%; height: 64.5px;
    background: var(--charcoal); color: #fff; text-align: center;
    font-family: 'Raleway', sans-serif; font-weight: 600; font-size: 11.3px;
    line-height: 13.8px; padding-top: 11px; text-transform: uppercase;
  }
</style>
</head>
<body>
<main class="stage">

  <section class="card card--front" aria-label="Card front">
    <div class="holder">
      <p class="holder__name">MARCUS T. HOLLINGS</p>
      <p class="holder__role">Project Manager</p>
    </div>

    <div class="wordmark wordmark--front">
      <span class="wordmark__square"></span>
      <span>Harbourline<br>Electrical<br>Solutions</span>
    </div>

    <p class="sectors">COMMERCIAL INDUSTRIAL RESIDENTIAL</p>

    <div class="contact">
      <p class="contact__row">
        <svg width="9" height="13" viewBox="0 0 9 13" aria-hidden="true">
          <rect x="0.8" y="0.8" width="7.4" height="11.4" rx="1.3" fill="none" stroke="#0d4f66" stroke-width="1.6"/>
          <rect x="3" y="9.4" width="3" height="1.2" fill="#0d4f66"/>
        </svg>
        (441) 555-0187
      </p>
      <p class="contact__row">
        <svg width="12" height="9" viewBox="0 0 12 9" aria-hidden="true">
          <rect x="0" y="0" width="12" height="9" fill="#0d4f66"/>
          <path d="M0.6 0.8 L6 5 L11.4 0.8" fill="none" stroke="#fff" stroke-width="1"/>
        </svg>
        hlelectricalsolutions@mailvento.com
      </p>
    </div>

    <div class="social">
      <div class="social__dots"><span class="social__dot"></span><span class="social__dot"></span></div>
      <p>@hlelectricalsolutions</p>
    </div>

    <svg class="front-bands" width="443" height="20" viewBox="0 0 443 20" aria-hidden="true">
      <polygon points="0,10 250,10 247,20 0,20" fill="#0f5468"/>
      <polygon points="254,2 443,2 443,20 248,20" fill="#4a4a4a"/>
    </svg>
  </section>

  <section class="card card--back" aria-label="Card back">
    <div class="wordmark wordmark--back">
      <span class="wordmark__square"></span>
      <span>Harbourline<br>Electrical<br>Solutions</span>
    </div>
    <div class="back__rule"></div>
    <div class="services">
      <p>Electrical Construction &amp; Maintenance</p>
      <p>LED Lighting &amp; Automation | Data &amp; Communication</p>
      <p>Life Safety Systems (Fire Alarm / Security)</p>
    </div>
  </section>

</main>
</body>
</html>
```